Executive recruiting firm in need of business card design

Executive recruiting firm looking for a sleek, classy and modern business card design; card itself will be square shape, rounded edges and soft touch paper, our colors are dark blues in the navy color scale, silvers and grays. Reference our website for a better idea of our company's feel and goals at Tarvex-Up.com - our company message is "Employee Engagement Begins at Recruitment" this should be on the card

```html
<!DOCTYPE html>
<html lang="en">
<head>
<meta charset="utf-8">
<title>Tarvex-Up Business Card</title>
<link rel="stylesheet" href="https://fonts.googleapis.com/css2?family=Roboto:wght@400;500;700&display=swap">
<style>
  :root {
    --navy: #181a4a;
    --ink: #3f4148;
    --paper: #f4f3f1;
    --silver: #8c8e94;
    --gray-band: #55575d;
    --divider: #c9c9cc;
    --backdrop: #e4ddd4;
  }
  * { margin: 0; padding: 0; box-sizing: border-box; }
  html, body { width: 1200px; height: 794px; overflow: hidden; }
  body { background: var(--backdrop); position: relative; font-family: "Roboto", sans-serif; }

  .card {
    position: absolute;
    width: 560px; height: 320px;
    background: var(--paper);
    border-radius: 4px;
    box-shadow: 0 2px 6px rgba(0,0,0,.12);
    overflow: hidden;
  }
  .card--front { left: 140px; top: 60px; }
  .card--back  { left: 500px; top: 414px; }

  .company-name {
    font-family: "Roboto", sans-serif;
    font-weight: 500;
    color: var(--navy);
    white-space: nowrap;
  }
  .card--front .company-name {
    position: absolute; left: 0; right: 0; top: 104px;
    text-align: center; font-size: 40px; line-height: 48px;
  }
  .slogan {
    position: absolute; left: 0; right: 0; bottom: 46px;
    text-align: center; font-size: 15px; color: var(--ink); letter-spacing: .3px;
  }

  .card--back .company-name {
    position: absolute; left: 0; width: 300px; top: 138px;
    text-align: center; font-size: 30px; line-height: 36px;
  }
  .divider { position: absolute; left: 300px; top: 30px; width: 1px; height: 230px; background: var(--divider); }

  .contact { position: absolute; left: 318px; top: 28px; color: var(--ink); }
  .contact__name { font-size: 18px; font-weight: 700; color: var(--navy); }
  .contact__role { font-size: 14px; font-weight: 500; color: var(--silver); margin-bottom: 12px; }
  .contact__address { font-size: 13px; line-height: 17px; color: var(--silver); margin-bottom: 10px; }
  .contact__list { list-style: none; font-size: 13.5px; line-height: 19px; }
  .contact__list li { display: flex; align-items: center; gap: 10px; }
  .contact__list svg { width: 13px; height: 13px; fill: var(--navy); flex: none; }

  .web-tab {
    position: absolute; right: 0; bottom: 0; width: 250px; height: 46px;
    background: var(--navy); border-top-left-radius: 46px 46px;
    color: #fff; font-size: 13px; letter-spacing: 2.5px;
    display: flex; align-items: center; justify-content: flex-end; padding-right: 18px;
  }
  .base-band { position: absolute; left: 0; bottom: 0; width: 310px; height: 8px; background: var(--gray-band); }
</style>
</head>
<body>

<section class="card card--front">
  <p class="company-name">Tarvex Up</p>
  <p class="slogan">Employee Engagement Begins at Recruitment</p>
</section>

<section class="card card--back">
  <p class="company-name">Tarvex Up</p>
  <div class="divider"></div>

  <div class="contact">
    <p class="contact__name">DANIEL REYES</p>
    <p class="contact__role">CEO/FOUNDER</p>
    <p class="contact__address">482 Linden Crest Ave.<br>Marlow Springs, CA</p>
    <ul class="contact__list">
      <li><svg viewBox="0 0 24 24"><path d="M6.6 10.8a15.1 15.1 0 0 0 6.6 6.6l2.2-2.2c.3-.3.7-.4 1-.2 1.1.4 2.3.6 3.6.6.6 0 1 .4 1 1V20c0 .6-.4 1-1 1A17 17 0 0 1 3 4c0-.6.4-1 1-1h3.5c.6 0 1 .4 1 1 0 1.3.2 2.5.6 3.6.1.3 0 .7-.2 1z"/></svg>555 214 3870</li>
      <li><svg viewBox="0 0 24 24"><path d="M7 1h10a2 2 0 0 1 2 2v18a2 2 0 0 1-2 2H7a2 2 0 0 1-2-2V3a2 2 0 0 1 2-2zm0 3v14h10V4zm5 15.5a1 1 0 1 0 0 2 1 1 0 0 0 0-2z"/></svg>555 390 6152</li>
      <li><svg viewBox="0 0 24 24"><path d="M7 2h10v5H7zM4 8h16a2 2 0 0 1 2 2v7h-4v5H6v-5H2v-7a2 2 0 0 1 2-2zm4 8v4h8v-4z"/></svg>555 728 4416</li>
      <li><svg viewBox="0 0 24 24"><path d="M2 5h20v14H2zm2 2v.5l8 5 8-5V7z"/></svg>daniel@tarvex-up.com</li>
    </ul>
  </div>

  <div class="base-band"></div>
  <div class="web-tab">www.tarvex-up.com</div>
</section>

</body>
</html>
```